Animal Eye Clinic needs a Business card

We are a new veterinary ophthalmology practice (Ridgeline Pet Vision Care) and we need a business card designed. We only see animal eyes - we are not a regular veterinary clinic. We already have a logo. We are looking for a professional, good looking business card to hand out to our clients. We are looking for something simple but professional and contemporary. Our logo is likely the only picture/graphic that needs to be on the card.
Updates

Contact Information for Business Card

Delia Vossman, BSc, DVM, MSc, DipACVO
Veterinary Ophthalmologist

Phone: 555.418.3927
Email: ridgelinepetvisioncare@mailbox-example.net
Website: ridgelinepetvisioncare-example.net
Address: 1874 Thornbury Rd
Larchmere, WV, V1X 4M9

Colors

Designer to choose colors to be used in the design.

Requirements
Must have
• Our logo (attached)

```html
<!DOCTYPE html>
<html lang="en">
<head>
<meta charset="utf-8">
<title>Ridgeline Pet Vision Care — Business Card</title>
<link href="https://fonts.googleapis.com/css2?family=Roboto:wght@300;400;500;700&display=swap" rel="stylesheet">
<style>
  :root {
    --bg: #1c1d1f;
    --teal: #0897a9;
    --teal-bright: #11a6b8;
    --card-dark: #2a2d30;
    --ink-dark: #2b2e31;
    --grey-text: #9aa0a4;
    --rule: #6b7175;
    --white: #ffffff;
    --watermark: rgba(255,255,255,0.025);
  }
  * { box-sizing: border-box; margin: 0; padding: 0; }
  html, body {
    width: 1200px; height: 800px; overflow: hidden;
    background: var(--bg);
    font-family: 'Roboto', Arial, sans-serif;
  }
  .stage {
    position: relative; width: 1200px; height: 800px;
    display: flex; align-items: center; justify-content: center; gap: 40px;
  }
  .card {
    position: relative; width: 530px; height: 303px;
    border-radius: 18px; overflow: hidden;
  }

  /* Front */
  .card--front {
    background: var(--teal);
    display: flex; flex-direction: column; align-items: center; justify-content: center;
  }
  .brand { display: flex; align-items: center; gap: 14px; position: relative; }
  .brand__mark { width: 40px; height: 40px; border-radius: 50%; flex: none; }
  .brand__name { font-weight: 700; font-size: 26px; letter-spacing: 0.5px; line-height: 1; white-space: nowrap; }
  .card--front .brand__mark { background: var(--ink-dark); }
  .card--front .brand__name { color: var(--ink-dark); }
  .front__web {
    margin-top: 34px; color: var(--white);
    font-size: 13px; letter-spacing: 2.4px; font-weight: 400;
  }

  /* Back */
  .card--back { background: var(--card-dark); padding: 30px 32px; }
  .back__watermark {
    position: absolute; right: -50px; top: -40px;
    width: 240px; height: 240px; border-radius: 50%;
    background: var(--watermark);
  }
  .card--back .brand__mark { background: var(--teal-bright); width: 34px; height: 34px; }
  .card--back .brand__name { color: var(--teal-bright); font-size: 21px; }
  .person { position: relative; margin-top: 40px; }
  .person__name { color: var(--teal-bright); font-weight: 700; font-size: 17px; }
  .person__title { color: var(--grey-text); font-size: 12.5px; margin-top: 4px; }
  .back__rule { position: relative; height: 1px; background: var(--rule); margin-top: 14px; }
  .back__footer {
    position: relative; display: flex; justify-content: space-between; align-items: flex-end;
    margin-top: 16px;
  }
  .contacts { list-style: none; }
  .contacts li {
    display: flex; align-items: center; gap: 8px;
    color: var(--grey-text); font-size: 11px; line-height: 1; margin-bottom: 7px;
  }
  .contacts .icon {
    width: 15px; height: 15px; border-radius: 50%; background: var(--teal-bright);
    display: flex; align-items: center; justify-content: center; flex: none;
  }
  .address {
    color: var(--grey-text); font-size: 11px; line-height: 1.5; text-align: right;
    margin-bottom: 7px;
  }
</style>
</head>
<body>
<main class="stage">

  <section class="card card--front" aria-label="Business card front">
    <div class="brand">
      <span class="brand__mark"></span>
      <span class="brand__name">Ridgeline Pet Vision Care</span>
    </div>
    <p class="front__web">ridgelinepetvisioncare-example.net</p>
  </section>

  <section class="card card--back" aria-label="Business card back">
    <span class="back__watermark"></span>
    <div class="brand">
      <span class="brand__mark"></span>
      <span class="brand__name">Ridgeline Pet Vision Care</span>
    </div>

    <div class="person">
      <p class="person__name">Delia Vossman, BSc, DVM, MSc, DipACVO</p>
      <p class="person__title">Veterinary Ophthalmologist</p>
    </div>

    <div class="back__rule"></div>

    <div class="back__footer">
      <ul class="contacts">
        <li>
          <span class="icon">
            <svg width="9" height="9" viewBox="0 0 24 24"><path fill="#2a2d30" d="M6.6 10.8a15 15 0 0 0 6.6 6.6l2.2-2.2a1 1 0 0 1 1-.25 11.4 11.4 0 0 0 3.6.57 1 1 0 0 1 1 1V20a1 1 0 0 1-1 1A17 17 0 0 1 3 4a1 1 0 0 1 1-1h3.5a1 1 0 0 1 1 1c0 1.25.2 2.45.57 3.6a1 1 0 0 1-.25 1z"/></svg>
          </span>
          555.418.3927
        </li>
        <li>
          <span class="icon">
            <svg width="9" height="9" viewBox="0 0 24 24"><path fill="#2a2d30" d="M2 5h20v14H2z"/><path fill="none" stroke="#11a6b8" stroke-width="2" d="M2 6l10 7 10-7"/></svg>
          </span>
          ridgelinepetvisioncare@mailbox-example.net
        </li>
        <li>
          <span class="icon">
            <svg width="9" height="9" viewBox="0 0 24 24" fill="none" stroke="#2a2d30" stroke-width="2.4"><circle cx="12" cy="12" r="9"/><path d="M3 12h18M12 3c3 3 3 15 0 18M12 3c-3 3-3 15 0 18"/></svg>
          </span>
          ridgelinepetvisioncare-example.net
        </li>
      </ul>
      <p class="address">1874 Thornbury Rd<br>Larchmere, WV, V1X 4M9</p>
    </div>
  </section>

</main>
</body>
</html>
```